Business Card for Coastal Tundrabridge Advisory

We need a business card for Coastal Tundrabridge Advisory. The company website address is provided below. The company logo is attached. We provide specialized permafrost services to the mining, transportation, and oil & gas industries. The card should be prepared for:
Matthias Korhonen, PhD.
Coastal Tundrabridge Advisory
PO Box 418259
Quillwater, Alaska 99642
Direct: +1-907-555-0143
Email: mkorhonen@tundrabridgeadvisory.example
Website: www.coastaltundrabridgeadvisory.example

```html
<!DOCTYPE html>
<html lang="en">
<head>
<meta charset="utf-8">
<title>Coastal Tundrabridge Advisory — Business Card</title>
<link rel="stylesheet" href="https://fonts.googleapis.com/css2?family=Roboto+Condensed:ital,wght@0,400;0,700;1,700&family=Montserrat:wght@500&display=swap">
<style>
  :root {
    --page-bg: #f1f1f1;
    --card-white: #ffffff;
    --band-grey: #8b8b8b;
    --band-black: #111111;
    --ink: #161616;
    --icon-line: #7a7a7a;
    --back-card: #3b3b3b;
    --back-mark: #1d1d1d;
  }
  * { box-sizing: border-box; }
  html, body {
    margin: 0;
    width: 1199px;
    height: 1200px;
    overflow: hidden;
    background: var(--page-bg);
  }
  .sheet {
    position: relative;
    width: 1199px;
    height: 1200px;
  }
  .card {
    position: absolute;
    left: 238px;
    width: 724px;
    height: 413px;
    border-radius: 30px;
    overflow: hidden;
  }
  .card--front { top: 155px; background: var(--card-white); }
  .card--back  { top: 650px; background: var(--back-card); }

  .front-band { position: absolute; inset: 0; width: 724px; height: 413px; }

  .brand-name {
    position: absolute;
    left: 0; right: 0;
    text-align: center;
    font-family: "Montserrat", sans-serif;
    font-weight: 500;
    text-transform: uppercase;
    margin: 0;
  }
  .card--front .brand-name {
    top: 66px;
    font-size: 25px;
    letter-spacing: 3px;
    color: var(--card-white);
  }
  .card--back .brand-name {
    top: 182px;
    font-size: 34px;
    letter-spacing: 4px;
    color: var(--back-mark);
  }

  .person {
    position: absolute;
    left: 52px;
    top: 226px;
    font-family: "Roboto Condensed", sans-serif;
    color: var(--ink);
  }
  .person-name {
    margin: 0;
    font-size: 28px;
    font-weight: 700;
    font-style: italic;
    letter-spacing: -0.3px;
    line-height: 1;
  }
  .person-role {
    margin: 4px 0 0;
    font-size: 9px;
    font-weight: 700;
    font-style: italic;
  }
  .address {
    margin: 24px 0 0;
    font-size: 14px;
    font-weight: 700;
    font-style: normal;
    line-height: 20px;
  }

  .contacts {
    position: absolute;
    right: 24px;
    top: 262px;
    margin: 0;
    padding: 0;
    list-style: none;
    font-family: "Roboto Condensed", sans-serif;
    font-weight: 700;
    font-size: 13.5px;
    color: var(--ink);
  }
  .contacts li {
    display: flex;
    align-items: center;
    justify-content: flex-end;
    height: 27.5px;
  }
  .contact-icon {
    width: 20px;
    height: 20px;
    margin-left: 16px;
    flex: none;
  }
</style>
</head>
<body>
<main class="sheet">

  <section class="card card--front" aria-label="Card front">
    <svg class="front-band" viewBox="0 0 724 413" aria-hidden="true">
      <path fill="var(--band-black)" d="M0 0 H724 V150 C610 150 500 200 362 205 C224 200 114 150 0 150 Z"/>
      <path fill="var(--band-grey)" d="M0 0 H724 V76 C600 76 540 96 470 150 C430 185 400 205 362 205 C324 205 294 185 254 150 C184 96 124 76 0 76 Z"/>
    </svg>
    <h1 class="brand-name">Coastal Tundrabridge Advisory</h1>

    <div class="person">
      <h2 class="person-name">Matthias Korhonen, PhD</h2>
      <p class="person-role">Founder &amp; Director</p>
      <address class="address">PO Box 418259<br>Quillwater, Alaska 99642</address>
    </div>

    <ul class="contacts">
      <li>+1-907-555-0143
        <svg class="contact-icon" viewBox="0 0 20 20" aria-hidden="true"><circle cx="10" cy="10" r="8.5" fill="none" stroke="var(--icon-line)"/><path d="M7 6 l1.6 -.4 1 2.2 -1 .8 c.5 1.2 1.3 2 2.5 2.5 l.8 -1 2.2 1 -.4 1.6 c-3.5 0 -6.7 -3.2 -6.7 -6.7z" fill="none" stroke="var(--icon-line)" stroke-width=".9"/></svg>
      </li>
      <li>(907) 555 0143
        <svg class="contact-icon" viewBox="0 0 20 20" aria-hidden="true"><circle cx="10" cy="10" r="8.5" fill="none" stroke="var(--icon-line)"/><rect x="7.2" y="5" width="5.6" height="10" rx="1" fill="none" stroke="var(--icon-line)" stroke-width=".9"/></svg>
      </li>
      <li>mkorhonen@tundrabridgeadvisory.example
        <svg class="contact-icon" viewBox="0 0 20 20" aria-hidden="true"><circle cx="10" cy="10" r="8.5" fill="none" stroke="var(--icon-line)"/><rect x="5.5" y="7" width="9" height="6" rx=".6" fill="none" stroke="var(--icon-line)" stroke-width=".9"/><path d="M5.5 7 L10 10.3 14.5 7" fill="none" stroke="var(--icon-line)" stroke-width=".9"/></svg>
      </li>
      <li>www.coastaltundrabridgeadvisory.example
        <svg class="contact-icon" viewBox="0 0 20 20" aria-hidden="true"><circle cx="10" cy="10" r="8.5" fill="none" stroke="var(--icon-line)"/><circle cx="10" cy="10" r="4.5" fill="none" stroke="var(--icon-line)" stroke-width=".9"/><ellipse cx="10" cy="10" rx="2" ry="4.5" fill="none" stroke="var(--icon-line)" stroke-width=".8"/><path d="M5.5 10 H14.5" stroke="var(--icon-line)" stroke-width=".8"/></svg>
      </li>
    </ul>
  </section>

  <section class="card card--back" aria-label="Card back">
    <h2 class="brand-name">Coastal Tundrabridge Advisory</h2>
  </section>

</main>
</body>
</html>
```